Flyer-Design für Ofenservice Firma
Zielgruppe
Die Firma hat als Kerngeschäft Wartung, Reinigung, Reparatur und Inbetriebnahme von Öfen und Kaminen aller Art. Der Fokus liegt dabei auf Pelletöfen. Die Firma versteht sich als zuverlässiger Dienstleister mit gutem Preisleistungsverhältnis. Zielgruppe sind hauptsächlich private Bewohner von Einfamilienhäusern in der ländlichen Gegend (Hessen)
Aufgabenstellung
Zur Bekanntmachung nach Neugründung soll ein Faltflyer gestaltet werden mit insgesamt 6 Bereichen. Die Informationen, welche auf den Flyer sollen, entnehmen Sie bitte dem Entwurf (flyer.pdf). Dieser stellt nur eine erste Idee dar und darf gerne nach Belieben verändert bzw. neu gestaltet werden. Die enthaltenen Informationen, sollten im Großen und Ganzen aber beibehalten werden. Schön wäre evtl. auch eine Hervorhebung der Preise, da wir Preisführer im Markt sind. Auch die Bilder unseres Teams sollen in den Flyer integriert sein. Auf Anfrage kann ich auch gerne weitere Kamin- und Ofenfotos zur Verfügung stellen, für welche ich die Nutzungsrechte habe. Falls Sie weitere Informationen benötigen oder Fragen haben, kommen Sie gerne auf mich zu. Die Bilder dürfen gerne etwas ausgeschnitten werden. Es geht in erster Linie darum, dass die Kunden erkennen, welche Art von Ofen sie zu Hause haben.

```html
<!DOCTYPE html>
<html lang="de">
<head>
<meta charset="utf-8">
<title>Ofenservice Faltflyer</title>
<link href="https://fonts.googleapis.com/css2?family=Jura:wght@400;500;600;700&display=swap" rel="stylesheet">
<style>
  :root{
    --paper:#f5f7fb;
    --ink:#4b5661;
    --heading:#56636e;
    --accent:#d95f0e;
    --white:#ffffff;
    --wood:#c98a4e;
    --plaster:#e9e6e1;
    --studio:#eeeff1;
    --uniform:#2a2a2c;
  }
  *{margin:0;padding:0;box-sizing:border-box}
  html,body{width:1200px;height:769px;overflow:hidden;background:var(--paper)}
  .flyer{position:relative;width:1200px;height:769px;overflow:hidden;background:var(--paper);
    font-family:"Jura",sans-serif;color:var(--ink);font-weight:500}
  .panel-title{position:absolute;top:15px;font-size:21px;letter-spacing:2.8px;color:var(--heading);font-weight:500;white-space:nowrap}
  .title-ovens{left:52px}
  .title-profile{left:410px}
  .title-more{left:884px}
  .oven-photos{position:absolute;left:0;top:54px;width:387px;height:316px;border:1px solid var(--accent);display:flex}
  .oven-photo{flex:1;height:100%}
  .oven-photo.cabin{background:linear-gradient(160deg,var(--wood) 0%,#e3b47c 45%,#f2efe9 70%,#b9653a 100%);border-right:1px solid var(--accent)}
  .oven-photo.modern{background:linear-gradient(180deg,#f7f6f3 0%,var(--plaster) 70%,#e2d8c6 100%)}
  .profile-text{position:absolute;left:411px;top:66px;width:372px;font-size:14.2px;line-height:19.2px;letter-spacing:-0.15px;hyphens:manual}
  .profile-text p{margin-bottom:19.2px}
  .services{position:absolute;left:813px;top:68px;width:384px;font-size:13px;line-height:17.4px;letter-spacing:-0.1px}
  .services h3{font-size:14.5px;font-weight:500;margin-bottom:17px}
  .services p{margin-bottom:17px}
  .pricing-intro{position:absolute;left:16px;top:400px;width:372px}
  .pricing-intro h2{font-size:18.5px;font-weight:500;color:var(--heading);margin-bottom:10px;white-space:nowrap}
  .pricing-intro p{font-size:13px;line-height:17.4px;margin-bottom:12px;letter-spacing:-0.1px}
  .team-photo{position:absolute;left:386px;top:388px;width:402px;height:290px;
    background:radial-gradient(ellipse at 50% 75%,var(--uniform) 0%,#3b3b3e 30%,var(--studio) 62%,var(--white) 100%)}
  .legal-link{position:absolute;left:899px;top:474px;font-size:18px;color:var(--heading);white-space:nowrap}
  .price-band{position:absolute;left:0;top:678px;width:1200px;height:91px;background:var(--accent);color:var(--white)}
  .price-box{position:absolute;top:18px;width:350px;font-size:13.5px;line-height:17.5px}
  .price-box h4{font-size:14.5px;font-weight:700;margin-bottom:1px;white-space:nowrap;letter-spacing:-0.2px}
  .price-row{display:flex;justify-content:space-between;white-space:nowrap}
  .box-standard{left:17px}
  .box-heated{left:411px;top:19px}
  .promo{position:absolute;left:812px;top:7px;width:380px;text-align:center;letter-spacing:2px;white-space:nowrap}
  .promo .big{font-size:19px;line-height:23px;font-weight:500}
  .promo .small{font-size:12px;line-height:15px}
</style>
</head>
<body>
<div class="flyer">
  <div class="panel-title title-ovens">Grund- und Kachelöfen</div>
  <div class="panel-title title-profile">Firmengeschichte / Profil</div>
  <div class="panel-title title-more">Weitere Leistungen</div>

  <div class="oven-photos">
    <div class="oven-photo cabin" role="img" aria-label="Foto: gemauerter Kachelofen mit Feuer in einem Holzhaus"></div>
    <div class="oven-photo modern" role="img" aria-label="Foto: weißer runder Grundofen mit schwarzer Sichtscheibe"></div>
  </div>

  <div class="profile-text">
    <p>Als Inhaber geführtes Unternehmen bieten wir professionelle Serviceleistungen rund um Öfen aller Art (Kaminöfen, Pelletöfen, Scheitholzöfen, Kachelöfen, offene Kamine, Grund- und Speicher&shy;öfen. Durch erfahrene Mitarbeiter, regelmäßigen Personalschulungen und der Zusammernarbeit mit namhaften Herstellern können wir Ihnen eine breite Palette an Dienstleistungen rund um Kaminöfen bieten.</p>
    <p>Guter Service muss nicht teuer sein !</p>
    <p>Überzeugen Sie sich von unserem Preisleistungs&shy;verhältnis sowie unseren exklusiven Konditionen bei Abschluss eines Wartungsvertrages.</p>
  </div>

  <div class="services">
    <h3>Reparatur und Instandsetzung:</h3>
    <p>Funktioniert Ihr Ofen nicht richtig, sind wir schnellst&shy;möglich für Sie da und setzen Ihren Ofen wieder instand.</p>
    <h3>Inbetriebnahme:</h3>
    <p>Sie haben einen neuen Ofen erworben und möchten sich über die richtige Nutzung und Befeuerung informieren?</p>
    <h3>Kaufberatung:</h3>
    <p>Sie planen eine Neuanschaffung und möchten sich vorab über Anschlussmöglichkeiten, Brennstoffarten und Modelle informieren?<br>Wir beraten Sie unabhängig und Ihre Bedürfnisse zugeschnitten.</p>
  </div>

  <div class="pricing-intro">
    <h2>Leistungsbeschreibung und Preise</h2>
    <p>Reinigung<br>Schamottverkleidungen, Sichtscheibe, Zwischenboden, gesamter Feuerraum, sämtliche Rauchgaszüge, Aschebehälter, Abgasrohre (bis zu 2m gestreckte Länge)</p>
    <p>Überprüfung<br>Dichtungen (Türdichtung, Türglasdichtung, Putz-<br>deckeldichtungen</p>
    <p>Probelauf des Gerätes</p>
  </div>

  <div class="team-photo" role="img" aria-label="Teamfoto: drei Mitarbeiter in schwarzer Arbeitskleidung mit erhobenem Daumen"></div>

  <div class="legal-link">Impressum / Disclaimer</div>

  <div class="price-band">
    <div class="price-box box-standard">
      <h4>Preise Kachelofen mit bis zu 4 Öffnungen</h4>
      <div class="price-row"><span>mit Wartungsvertrag:</span><span>€ 350 inkl. MWST</span></div>
      <div class="price-row"><span>ohne Wartungsvertrag:</span><span>€ 390 inkl. MWST</span></div>
    </div>
    <div class="price-box box-heated">
      <h4>Preise Kachelofen mit nachgeschalteter Heizfläche</h4>
      <div class="price-row"><span>mit Wartungsvertrag:</span><span>€ 250 inkl. MWST</span></div>
      <div class="price-row"><span>ohne Wartungsvertrag:</span><span>€ 290 inkl. MWST</span></div>
    </div>
    <div class="promo">
      <div class="big">AKTION 50€</div>
      <div class="big">für Neukundenwerbung</div>
      <div class="small">(bei Abschluss eines Wartungsvertrages)</div>
    </div>
  </div>
</div>
</body>
</html>
```